Web Design Project for Communications Agency

The design I need (PSD file) is for an agency offering specialised PR and communications services for customers in the healthcare sector.

OBJECTIVES OF THE WEBSITE:
1. To promote the agency's communication services
2. To position Solène Brivard as an industry leader, an expert in healthcare PR and communications by highlighting blogposts and social media.

WHAT I NEED:
1st, I need the design for the Home Page ONLY.
Once approved, I will need the other pages designed as well. (Here is prototype that we've already developed for the Website that will guide you in the design:
http://qorvelle.net/solenebrivard/)

VISUAL INSPIRATION
We want to give this Website a "Flat Design" look. Here are some websites for inspiration :
- http://tavrolinkworks.com/#!/process
- http://www.brindlemoss.co/
- http://quellaroft.com/

Also, reuse images found on the company's current Website :
http://www.solenebrivard.com/fr/index.html

HOMEPAGE MAIN ELEMENTS:
1. Main menu : 6 sections
Accueil | Agence | Services | Approche | Publications | Contact

2. Main Call To Action (big dark rectangle in prototype):
Can be slider or just an information bloc.

3. Publications récentes :
The 4 latest blog posts must be features on the homepage (will be linked with the "Publications" section)

4. Dynamic Footer :
Contains a Chirpfeed feed and a Subscribe to our Newsletter feature (revecez nos publications)

OTHER PAGES (to design once Homepage is approved)
- Agence (about us)
- Services (our team)
- Approche (our approach)
- Publications (blog articles)
- Contact (Contact us)

Industry/Entity Type

Communications

Requirements
Must have
• Please refer to prototype :
http://qorvelle.net/solenebrivard/
Must have ALL features present in prototype.

Also, must reuse this picture in the design : http://solenebrivard.com/static/images/home-big-box.jpg

Finally, you will find attached the company logo.

```html
<!DOCTYPE html>
<html lang="fr">
<head>
<meta charset="utf-8">
<title>Solène Brivard — Gestion d'enjeux, affaires publiques</title>
<link rel="stylesheet" href="https://fonts.googleapis.com/css2?family=PT+Sans:wght@400;700&family=PT+Sans+Narrow:wght@400;700&display=swap">
<style>
:root{
  --red:#c12d3f;
  --red-dark:#a3202f;
  --red-deep:#9c1c2c;
  --ink:#222;
  --text:#555;
  --grey-band:#e6e6e6;
  --grey-hero:#e3e3e3;
  --page:#f4f4f4;
  --footer-dark:#3a3a3a;
  --link-blue:#8fd0f2;
  --orange:#e0662a;
}
*{box-sizing:border-box;margin:0;padding:0}
html,body{width:694px;height:1200px;overflow:hidden}
body{background:var(--page);font-family:"PT Sans",sans-serif;color:var(--text);position:relative}

.site-header{position:absolute;left:0;top:0;width:694px;height:80px;background:#fff}
.brand{position:absolute;left:106px;top:6px;color:var(--red);font-family:"PT Sans Narrow",sans-serif;font-weight:400;font-size:31px;line-height:28px;letter-spacing:-0.5px}
.brand-tagline{position:absolute;left:106px;top:85px;font-family:"PT Sans Narrow",sans-serif;font-weight:700;font-size:10.5px;line-height:12px;color:#555;letter-spacing:.3px}
.brand-tagline::after{content:"";display:block;width:22px;height:2px;background:var(--red);margin-top:3px}
.social{position:absolute;left:458px;top:11px;display:flex;gap:7px}
.social span{width:16px;height:16px;border-radius:2px;display:block}
.lang{position:absolute;left:497px;top:41px;width:89px;height:16px;border:1px solid #ccc;background:#fff;font-size:7px;color:#999;padding:3px 0 0 21px;font-style:italic}
.lang .flag{position:absolute;left:5px;top:4px;width:11px;height:7px;background:#3c4d8f}
.lang .caret{position:absolute;right:8px;top:5px;width:4px;height:4px;border-right:1px solid #555;border-bottom:1px solid #555;transform:rotate(45deg)}

.main-nav{position:absolute;left:0;top:80px;width:694px;height:32px;background:linear-gradient(#ececec,#dedede);border-top:1px solid #d6d6d6}
.main-nav ul{list-style:none;position:absolute;left:278px;top:0;display:flex;height:32px}
.main-nav li{font-size:9px;color:#333;height:32px;line-height:32px;padding:0 9px;border-right:1px solid #d0d0d0}
.main-nav li.active{background:#1e1e1e;color:#fff}

.hero{position:absolute;left:0;top:112px;width:694px;height:240px;background:var(--grey-hero)}
.hero-visual{position:absolute;left:96px;top:2px;width:220px;height:226px;background:radial-gradient(ellipse at 50% 40%,#fafafa 0%,#e2e2e2 60%,#d6d6d6 100%);border-radius:6px}
.hero-visual::before{content:"";position:absolute;left:36px;top:10px;width:110px;height:55px;background:linear-gradient(#c8323f,#a52331);opacity:.8;border-radius:4px}
.hero-text{position:absolute;left:332px;top:66px;width:233px;font-size:11.5px;line-height:14px;color:#111;text-align:justify}
.btn-red{position:absolute;left:337px;top:120px;width:125px;height:22px;background:linear-gradient(#d13a4b,var(--red-dark));border-radius:4px;color:#fff;font-size:11px;line-height:22px;text-align:center}
.hero-arrow{position:absolute;top:92px}

.section-title{position:absolute;left:120px;top:361px;width:451px;height:29px}
.section-title::before{content:"";position:absolute;left:0;right:0;top:10px;border-top:1px solid #999}
.section-title h2{position:absolute;left:145px;top:0;width:161px;height:29px;background:var(--red);color:#fff;font-weight:400;font-size:15px;line-height:27px;text-align:center;border-radius:2px}

.post{position:absolute;left:126px;width:445px;height:110px}
.post-thumb{position:absolute;left:0;top:0;width:172px;height:108px;border:1px solid #ccc;border-radius:3px;box-shadow:0 3px 3px rgba(0,0,0,.15)}
.post-body{position:absolute;left:184px;top:0;width:256px}
.post-title{font-weight:400;font-size:10px;color:var(--red);line-height:12px}
.post-date{font-size:6.5px;color:#555;margin-top:6px}
.post-body p{font-size:6.3px;line-height:9.2px;text-align:justify;margin-top:7px;color:#555}
.post-more{display:block;font-size:6.5px;color:var(--red);margin:6px 0 0 5px}
.post-more::after{content:"";display:inline-block;width:6px;height:6px;border-radius:50%;background:var(--orange);margin-left:7px;vertical-align:-1px}

.site-footer{position:absolute;left:0;top:957px;width:694px;height:199px;background:linear-gradient(var(--red) 0%,var(--red-deep) 100%)}
.feed{position:absolute;left:0;top:0;width:358px;height:199px;border-right:1px solid rgba(0,0,0,.15);box-shadow:1px 0 0 rgba(255,255,255,.08)}
.feed-brand{position:absolute;left:133px;top:15px;display:flex;align-items:center;gap:10px;color:var(--link-blue);font-size:28px;font-weight:700}
.feed-brand .dot{width:26px;height:26px;border-radius:50%;background:var(--link-blue)}
.tweet{position:absolute;left:133px;width:190px;font-size:8.2px;line-height:10.4px;color:#fff}
.tweet .tag{color:var(--link-blue)}
.btn-dark{position:absolute;height:19px;background:linear-gradient(#3a3a3a,#0c0c0c);color:#fff;font-family:"PT Sans Narrow",sans-serif;font-weight:700;font-size:9.5px;line-height:19px;text-align:center;border-radius:2px}
.subscribe h3{position:absolute;left:400px;top:19px;color:#fff;font-weight:400;font-size:15px}
.field{position:absolute;left:400px;width:167px;height:18px;background:#fff;border:1px solid #ddd;border-radius:2px;font-size:6.5px;font-style:italic;color:#999;padding:4px 9px}

.legal{position:absolute;left:0;top:1156px;width:694px;height:44px;background:var(--footer-dark);color:#eee;font-size:6px}
.legal .copy{position:absolute;right:114px;top:12px}
.legal .scale{position:absolute;right:114px;top:26px}
</style>
</head>
<body>

<header class="site-header">
  <div class="brand">solène<br>brivard</div>
  <div class="social" aria-label="Réseaux sociaux">
    <span style="background:#3b5998"></span>
    <span style="background:#3ab0e2"></span>
    <span style="background:#333"></span>
    <span style="background:#f09c17"></span>
    <span style="background:#c4302b"></span>
    <span style="background:#7f97a8"></span>
  </div>
  <div class="lang"><span class="flag"></span>English<span class="caret"></span></div>
</header>

<nav class="main-nav">
  <ul>
    <li class="active">Accueil</li><li>Agence</li><li>Services</li><li>Approche</li><li>Publications</li><li style="border-right:0">Contact</li>
  </ul>
</nav>
<div class="brand-tagline">GESTION D'ENJEUX<br>AFFAIRES PUBLIQUES</div>

<section class="hero">
  <div class="hero-visual" role="img" aria-label="Cube blanc dont la face supérieure forme une croix rouge"></div>
  <p class="hero-text">Cabinet-conseil en communications et affaires publiques spécialisé dans le secteur de la santé.</p>
  <a class="btn-red">En savoir plus</a>
  <svg class="hero-arrow" style="left:41px" width="29" height="29" viewBox="0 0 29 29"><circle cx="14.5" cy="14.5" r="13" fill="#f2f2f2" stroke="#bbb" stroke-width="2"/><path d="M16.5 10l-4.5 4.5 4.5 4.5" fill="none" stroke="#333" stroke-width="2.4"/></svg>
  <svg class="hero-arrow" style="left:613px" width="29" height="29" viewBox="0 0 29 29"><circle cx="14.5" cy="14.5" r="13" fill="#f2f2f2" stroke="#bbb" stroke-width="2"/><path d="M12.5 10l4.5 4.5-4.5 4.5" fill="none" stroke="#333" stroke-width="2.4"/></svg>
</section>

<div class="section-title"><h2>Publication récentes</h2></div>

<article class="post" style="top:408px">
  <div class="post-thumb" role="img" aria-label="Photo : mains autour d'un ordinateur portable affichant un graphique" style="background:linear-gradient(135deg,#3a3a3a,#6b6b6b 50%,#2c2c2c)"></div>
  <div class="post-body">
    <h3 class="post-title">Duis Aute Irure Dolor Reprehenderit Voluptate Cillum</h3>
    <div class="post-date">23 juillet 2013</div>
    <p>Lorem ipsum dolor sit amet, consectetur adipisicing elit, sed do eiusmod tempor incididunt ut labore et dolore magna aliqua. Ut enim ad minim veniam, quis nostrud exercitation ullamco laboris nisi ut aliquip ex ea commodo consequat.</p>
    <p>Excepteur sint occaecat cupidatat non proident, sunt in culpa qui officia deserunt mollit anim id est laborum.Velit esse cillum dolore eu fugiat nulla pariatur.</p>
    <a class="post-more">Article complet</a>
  </div>
</article>

<article class="post" style="top:547px">
  <div class="post-thumb" role="img" aria-label="Photo : poignée de main entre collègues en costume" style="background:linear-gradient(135deg,#eef0f2,#8a96a6 55%,#2d3440)"></div>
  <div class="post-body">
    <h3 class="post-title">Duis Aute Irure Dolor Reprehenderit Voluptate Cillum</h3>
    <div class="post-date">23 juillet 2013</div>
    <p>Lorem ipsum dolor sit amet, consectetur adipisicing elit, sed do eiusmod tempor incididunt ut labore et dolore magna aliqua. Ut enim ad minim veniam, quis nostrud exercitation ullamco laboris nisi ut aliquip ex ea commodo consequat.</p>
    <p>Excepteur sint occaecat cupidatat non proident, sunt in culpa qui officia deserunt mollit anim id est laborum.Velit esse cillum dolore eu fugiat nulla pariatur.</p>
    <a class="post-more">Article complet</a>
  </div>
</article>

<article class="post" style="top:686px">
  <div class="post-thumb" role="img" aria-label="Photo : professionnelle souriante devant une équipe de bureau" style="background:linear-gradient(135deg,#a9c3d6,#d9d2c8 50%,#4a4a4e)"></div>
  <div class="post-body">
    <h3 class="post-title">Duis Aute Irure Dolor Reprehenderit Voluptate Cillum</h3>
    <div class="post-date">23 juillet 2013</div>
    <p>Lorem ipsum dolor sit amet, consectetur adipisicing elit, sed do eiusmod tempor incididunt ut labore et dolore magna aliqua. Ut enim ad minim veniam, quis nostrud exercitation ullamco laboris nisi ut aliquip ex ea commodo consequat.</p>
    <p>Excepteur sint occaecat cupidatat non proident, sunt in culpa qui officia deserunt mollit anim id est laborum.Velit esse cillum dolore eu fugiat nulla pariatur.</p>
    <a class="post-more">Article complet</a>
  </div>
</article>

<article class="post" style="top:825px">
  <div class="post-thumb" role="img" aria-label="Photo : tableau blanc avec schéma manuscrit de planification" style="background:linear-gradient(135deg,#f2f2f2,#e0e0e0 60%,#d3c9c9)"></div>
  <div class="post-body">
    <h3 class="post-title">Duis Aute Irure Dolor Reprehenderit Voluptate Cillum</h3>
    <div class="post-date">23 juillet 2013</div>
    <p>Lorem ipsum dolor sit amet, consectetur adipisicing elit, sed do eiusmod tempor incididunt ut labore et dolore magna aliqua. Ut enim ad minim veniam, quis nostrud exercitation ullamco laboris nisi ut aliquip ex ea commodo consequat.</p>
    <p>Excepteur sint occaecat cupidatat non proident, sunt in culpa qui officia deserunt mollit anim id est laborum.Velit esse cillum dolore eu fugiat nulla pariatur.</p>
    <a class="post-more">Article complet</a>
  </div>
</article>

<footer class="site-footer">
  <div class="feed">
    <div class="feed-brand"><span class="dot"></span>chirpfeed</div>
    <p class="tweet" style="top:62px">Velit esse cillum dolore eu fugiat nulla pariatur. Excepteur sint occaecat cupidatat non proident. <span class="tag">@SoleneBrivard #EnjeuSanté</span></p>
    <p class="tweet" style="top:103px">Velit esse eu fugiat nulla pariatur. Excepteur sint occaecat cupidatat non proident. <span class="tag">@SoleneBrivard #EnjeuSanté</span></p>
    <a class="btn-dark" style="left:166px;top:146px;width:115px">Suivre@SoleneBrivard</a>
  </div>
  <div class="subscribe">
    <h3>Recevez nos publications</h3>
    <div class="field" style="top:55px">Votre nom</div>
    <div class="field" style="top:88px">Votre courriel</div>
    <a class="btn-dark" style="left:478px;top:121px;width:88px">Abonnez-vous</a>
  </div>
</footer>

<div class="legal">
  <span class="copy">© 2013 solenebrivard, All rights reserved</span>
  <span class="scale">x2</span>
</div>

</body>
</html>
```